Website for IT consulting Company

I need a website upgrade, the existing site content is ok, I would also like to add a testimonial page, the site should be something that is easy for us to update content. You use the content from www.kelvanbrook.com as an example. I will also post update logo and artwork. I also need a contact form with some type of validation or captcha.

I added Coded to the Project

Please omit Address maps

Target Market(s)

small business, service oriented companies. We provide IT Consulting, support and mangement

Industry/Entity Type

Information Technology

Coding

Number of Pages Required

1 page

Font styles to use
Serif
Sans Serif

Requirements
Must have
• Contain logo attached, and content from existing web site www.kelvanbrook.com.
• Also need to update content easily, and be movable to different platforms.
• There is a catch phrase
• "Let us worry about your technology…” “ so you don’t have to!”
• Should be included.
Nice to have
• Testimonial page, Project page where we can post new and past projects and pictures
Should not have
• none

```html
<!DOCTYPE html>
<html lang="en">
<head>
<meta charset="utf-8">
<title>Kelvanbrook – IT Solutions</title>
<link rel="stylesheet" href="https://fonts.googleapis.com/css2?family=Raleway:wght@300;400;600;700&family=Open+Sans:ital,wght@0,400;0,600;0,700;1,400&display=swap">
<style>
:root{
  --orange:#f58a21;
  --orange-dark:#e07412;
  --ink:#222;
  --text:#555;
  --grey-bg:#f3f3f3;
  --slate:#5d5f63;
  --footer:#1f2329;
  --white:#fff;
}
*{box-sizing:border-box;margin:0;padding:0}
html,body{width:1200px;height:2941px;overflow:hidden;background:#fff}
body{position:relative;font-family:"Open Sans",Arial,sans-serif;color:var(--text)}
.abs{position:absolute}
.brand{font-family:"Raleway",Arial,sans-serif;font-weight:700;letter-spacing:1px;display:flex;align-items:center;gap:10px}
.brand .mark{width:22px;height:22px;background:var(--orange)}
/* header */
.site-header{position:absolute;left:0;top:0;width:1200px;height:100px;background:#fff}
.site-header .brand{position:absolute;left:78px;top:30px;font-size:30px;color:#555}
.nav{position:absolute;right:56px;top:48px;display:flex;gap:28px;font-family:"Raleway",sans-serif;font-size:17px;color:#666}
.nav .active{color:var(--orange);border-bottom:2px solid var(--orange);padding-bottom:6px}
/* hero */
.hero{position:absolute;left:0;top:100px;width:1200px;height:580px;background:linear-gradient(100deg,#d9dcdf 0%,#eef0f1 45%,#cfd6d9 100%)}
.hero-rule{position:absolute;left:0;top:678px;width:1200px;height:3px;background:var(--orange)}
.hero-title{position:absolute;right:80px;top:120px;text-align:right;font-family:"Open Sans",sans-serif;font-weight:600;font-size:50px;line-height:63px;color:var(--orange);text-transform:uppercase}
.hero-sub{position:absolute;right:80px;top:248px;font-size:28px;color:#222}
.btn{display:inline-block;background:var(--orange);color:#fff;font-size:19px;text-transform:uppercase;border-radius:3px;text-align:center}
.hero .btn{position:absolute;left:956px;top:315px;width:164px;height:51px;line-height:51px}
.arrow{position:absolute;top:399px;width:48px;height:48px;border:2px solid rgba(255,255,255,.85);border-radius:50%;background:rgba(0,0,0,.08)}
.divider{position:absolute;left:580px;width:40px;height:40px;border-radius:50%;background:#fff;box-shadow:0 0 0 4px #fff}
.divider::after{content:"";position:absolute;left:11px;top:11px;width:18px;height:18px;border-radius:50%;background:var(--orange)}
/* welcome */
.section-title{position:absolute;left:0;width:1200px;text-align:center;font-family:"Raleway",sans-serif;font-weight:700;font-size:42px;color:var(--ink)}
.section-title span{color:var(--orange)}
.welcome-text{position:absolute;left:160px;top:795px;width:880px;text-align:center;font-size:15.5px;line-height:26px;color:#555}
/* services */
.services{position:absolute;left:0;top:1055px;width:1200px;height:500px;background:var(--grey-bg)}
.title-rule{position:absolute;left:530px;width:140px;height:1px;background:#ccc}
.service{position:absolute;top:145px;width:340px;text-align:center}
.service .icon{width:132px;height:132px;margin:0 auto;border-radius:18px;background:var(--orange);border:3px solid #fff;box-shadow:0 0 0 2px var(--orange);display:flex;align-items:center;justify-content:center}
.service .icon.grey{background:#7b7b7b;box-shadow:0 0 0 2px #7b7b7b}
.service h3{font-family:"Raleway",sans-serif;font-weight:400;font-size:23px;color:#333;margin-top:42px;line-height:28px}
.service p{font-size:14px;line-height:22px;color:#666;margin-top:8px}
/* flexible */
.flex-left{position:absolute;left:0;top:1555px;width:600px;height:465px;background:var(--slate)}
.flex-right{position:absolute;left:600px;top:1555px;width:600px;height:465px;background:linear-gradient(90deg,#ee8a2a,#f08a22)}
.flex-left h2{position:absolute;left:78px;top:48px;font-family:"Raleway",sans-serif;font-weight:600;font-size:40px;color:#fff}
.flex-left p{position:absolute;left:78px;top:124px;width:460px;font-size:16px;line-height:25px;color:#f0f0f0}
.flex-list{position:absolute;left:78px;top:247px;list-style:none;color:#fff;font-size:16px}
.flex-list li{height:41.5px;display:flex;align-items:center;gap:14px;text-transform:uppercase}
.flex-list li::before{content:"›";display:inline-block;width:16px;height:16px;border-radius:50%;background:#fff;color:var(--slate);font-size:15px;line-height:14px;text-align:center;font-weight:700}
.feature-list{position:absolute;left:90px;top:52px;list-style:none}
.feature-list li{height:62px;display:flex;align-items:center;gap:22px;font-family:"Raleway",sans-serif;font-weight:700;font-size:19px;color:#fff}
.feature-list svg{width:44px;height:44px;flex:none}
/* testimonials */
.testimonial{position:absolute;top:2160px;width:520px}
.avatar{position:absolute;left:0;top:0;width:152px;height:152px;border-radius:50%;background:linear-gradient(135deg,#c9c4bd,#8c8a87);border:4px solid #fff;box-shadow:0 0 0 2px #999}
.testimonial blockquote{position:absolute;left:195px;top:-4px;width:250px;text-align:center;font-size:14px;line-height:22px;color:#555}
.testimonial .name{position:absolute;left:195px;top:110px;width:250px;text-align:center;font-weight:700;font-size:17px;color:#222;text-transform:uppercase}
.testimonial .role{position:absolute;left:195px;top:140px;width:250px;text-align:center;font-style:italic;font-size:13px;color:#777}
.clients-rule{position:absolute;left:78px;width:1044px;height:1px;background:#f3c48f}
.clients{position:absolute;left:78px;top:2398px;width:1044px;display:flex;justify-content:space-between;align-items:center;height:64px}
.client{font-family:"Open Sans",sans-serif;font-weight:600;font-size:19px;color:#8a8a8a;display:flex;align-items:center;gap:8px}
.client i{display:inline-block;width:16px;height:16px;background:#bbb}
/* footer */
.site-footer{position:absolute;left:0;top:2535px;width:1200px;height:345px;background:linear-gradient(180deg,#2a2f36,#15181d)}
.site-footer .brand{position:absolute;left:78px;top:108px;font-size:30px;color:#fff}
.site-footer .brand .mark{background:#fff}
.social{position:absolute;top:186px;width:48px;height:48px;border-radius:50%;border:2px solid #fff;display:flex;align-items:center;justify-content:center;color:#fff;font-size:16px}
.social.filled{background:var(--orange);border-color:var(--orange)}
.footer-head{position:absolute;top:42px;font-family:"Open Sans",sans-serif;font-weight:700;font-size:18px;color:var(--orange);text-transform:uppercase}
.quick-links{position:absolute;left:355px;top:86px;list-style:none;font-size:13.5px;color:#ccc}
.quick-links li{height:26px}
.quick-links li::before{content:"›";margin-right:12px;color:#aaa}
.quick-links li:first-child{color:#fff}
.contact-row{position:absolute;left:533px;display:flex;gap:14px;font-size:13.5px;line-height:22px;color:#ddd}
.contact-row svg{flex:none;margin-top:3px}
.field{position:absolute;border:1px solid #ddd;background:transparent;color:#fff;font-size:13.5px;padding:10px 14px}
.submit{position:absolute;left:737px;top:229px;width:121px;height:49px;line-height:49px;font-size:18px;font-weight:700}
.bottom-bar{position:absolute;left:0;top:2878px;width:1200px;height:63px;background:var(--orange);text-align:center;line-height:63px;color:#fff;font-size:14px;font-weight:600}
</style>
</head>
<body>

<header class="site-header">
  <div class="brand"><span class="mark"></span>KELVANBROOK</div>
  <nav class="nav">
    <span class="active">Home</span><span>About</span><span>Services</span><span>Projects</span><span>Testimonials</span><span>Support</span><span>Careers</span><span>Contact</span>
  </nav>
</header>

<section class="hero" role="img" aria-label="Photo of a young man in glasses at a laptop in a bright office">
  <h1 class="hero-title">IT Solutions that work<br>for your business.</h1>
  <p class="hero-sub">A full service technology company.</p>
  <span class="btn">Contact Us</span>
  <span class="arrow" style="left:999px"><svg width="44" height="44" viewBox="0 0 44 44"><path d="M25 15 L18 22 L25 29" fill="none" stroke="#fff" stroke-width="2.5"/></svg></span>
  <span class="arrow" style="left:1072px"><svg width="44" height="44" viewBox="0 0 44 44"><path d="M19 15 L26 22 L19 29" fill="none" stroke="#fff" stroke-width="2.5"/></svg></span>
</section>
<div class="hero-rule"></div>
<span class="divider" style="top:658px"></span>

<section class="welcome">
  <h2 class="section-title" style="top:720px"><span>Welcome to</span> Kelvanbrook</h2>
  <p class="welcome-text">Outsourcing is subcontracting a process, such as product design or manufacturing, to a third-party company.[1] The decision to outsource is often made in the interest of lowering firm costs, redirecting or conserving energy directed at the competencies of a particular business, or to make more efficient use of land, labor, capital, (information) technology and resources. Outsourcing became part of the business lexicon during the 1980s.</p>
  <span class="btn abs" style="left:515px;top:929px;width:167px;height:49px;line-height:49px;font-size:18px">Read More</span>
</section>
<span class="divider" style="top:1030px"></span>

<section class="services">
  <h2 class="section-title" style="top:48px">Our <span>Services</span></h2>
  <span class="title-rule" style="top:107px"></span>
  <div class="service" style="left:75px">
    <div class="icon"><svg width="70" height="60" viewBox="0 0 70 60" fill="none" stroke="#fff" stroke-width="3"><rect x="4" y="4" width="62" height="38" rx="3"/><path d="M35 42v10M20 54h30"/><circle cx="35" cy="23" r="8"/><circle cx="35" cy="23" r="3"/></svg></div>
    <h3>Managed IT Solutions</h3>
    <p>Our staff will design, service, administer and maintain your IT needs. We are well versed on all major operating system, and network appliances</p>
  </div>
  <div class="service" style="left:430px">
    <div class="icon grey"><svg width="70" height="60" viewBox="0 0 70 60" fill="none" stroke="#fff" stroke-width="3"><rect x="4" y="4" width="62" height="38" rx="3"/><path d="M35 42v10M20 54h30M22 32l20-18M40 12l6 6"/></svg></div>
    <h3>Remote Diagnostic &amp; Support</h3>
    <p>Do you need a quick solution to a technical problem? With our live remote-assistance tool, a member of our support team can view your desktop and share control of your mouse.</p>
  </div>
  <div class="service" style="left:786px">
    <div class="icon"><svg width="70" height="60" viewBox="0 0 70 60" fill="none" stroke="#fff" stroke-width="3"><rect x="4" y="4" width="62" height="38" rx="3"/><path d="M35 42v10M20 54h30M22 19h26M42 14l6 5-6 5M48 28H22M28 23l-6 5 6 5"/></svg></div>
    <h3>IT Infrastructure Design &amp;<br>Installation</h3>
    <p>Do you have more than one site? Do you need remote access? We can design and implement LANS/WANS and VPN's.</p>
  </div>
</section>
<span class="divider" style="top:1535px"></span>

<section class="flex-left" role="img" aria-label="Muted photo of colleagues working in an office, grey overlay">
  <h2>Flexible Solutions</h2>
  <p>Kelvanbrook is a technology solution provider based in Houston, Texas. Our goal is to make technology a non-issue for individuals and small to medium size businesses ranging from 5 to 150 Users.</p>
  <ul class="flex-list">
    <li>Telecommunications.</li><li>Disaster Recovery.</li><li>Audio/Video Multimedia.</li><li>Web Design.</li>
  </ul>
</section>
<section class="flex-right" role="img" aria-label="Photo of a hand holding a light bulb, orange overlay">
  <ul class="feature-list" style="top:44px">
    <li><svg viewBox="0 0 44 44" fill="none" stroke="#fff" stroke-width="2"><rect x="16" y="4" width="12" height="9"/><rect x="4" y="30" width="12" height="9"/><rect x="28" y="30" width="12" height="9"/><path d="M22 13v8M10 30v-9h24v9"/></svg>Network Administration.</li>
    <li><svg viewBox="0 0 44 44" fill="none" stroke="#fff" stroke-width="2"><rect x="4" y="6" width="36" height="24" rx="2"/><path d="M22 30v6M14 38h16M14 22l8-8 4 4 6-6"/></svg>Desktop Support.</li>
    <li><svg viewBox="0 0 44 44" fill="none" stroke="#fff" stroke-width="2"><rect x="6" y="8" width="20" height="16"/><path d="M16 24v14M26 16h12v22M30 38h12"/></svg>Network Cabling</li>
    <li><svg viewBox="0 0 44 44" fill="none" stroke="#fff" stroke-width="2"><rect x="4" y="26" width="36" height="10" rx="2"/><path d="M14 18a11 11 0 0 1 16 0M9 13a18 18 0 0 1 26 0M19 22a4 4 0 0 1 6 0"/></svg>Wireless Networks.</li>
    <li><svg viewBox="0 0 44 44" fill="none" stroke="#fff" stroke-width="2"><path d="M22 4l15 6v11c0 10-7 16-15 19C14 37 7 31 7 21V10z"/><path d="M15 22l5 5 10-10"/></svg>Antivirus Solutions.</li>
    <li><svg viewBox="0 0 44 44" fill="none" stroke="#fff" stroke-width="2"><circle cx="20" cy="20" r="15"/><path d="M5 20h30M20 5c-6 8-6 22 0 30M20 5c6 8 6 22 0 30"/><rect x="27" y="29" width="13" height="11" fill="#f08a22"/><path d="M30 29v-3a3.5 3.5 0 0 1 7 0v3"/></svg>Network Security.</li>
  </ul>
</section>
<span class="divider" style="top:2000px"></span>

<section class="clients-say">
  <h2 class="section-title" style="top:2066px">What <span>Clients</span> Say</h2>
  <article class="testimonial" style="left:81px">
    <div class="avatar" role="img" aria-label="Portrait photo of a client"></div>
    <blockquote>"Lorem Ipsum is simply dummy text of the printing and typesetting industry. Lorem Ipsum has been the industry's standard dummy text ever since the 1500s."</blockquote>
    <div class="name">Clara Wendel</div>
    <div class="role">CEO,Company Name</div>
  </article>
  <article class="testimonial" style="left:624px">
    <div class="avatar" role="img" aria-label="Portrait photo of a client"></div>
    <blockquote>"Lorem Ipsum is simply dummy text of the printing and typesetting industry. Lorem Ipsum has been the industry's standard dummy text ever since the 1500s."</blockquote>
    <div class="name">Marcus Hale</div>
    <div class="role">CEO,Company Name</div>
  </article>
  <span class="clients-rule" style="top:2366px"></span>
  <div class="clients">
    <span class="client">Trailmark</span>
    <span class="client">Westfield College</span>
    <span class="client"><i></i>Corvane Media</span>
    <span class="client">Northridge University</span>
    <span class="client">Telvix</span>
    <span class="client">Summit Council</span>
  </div>
  <span class="clients-rule" style="top:2490px"></span>
</section>

<footer class="site-footer" role="contentinfo">
  <div class="brand"><span class="mark"></span>KELVANBROOK</div>
  <span class="social filled" style="left:94px">f</span>
  <span class="social" style="left:156px">g+</span>
  <span class="social" style="left:219px">t</span>

  <h4 class="footer-head" style="left:355px">Quick Links</h4>
  <ul class="quick-links">
    <li>Home</li><li>About Us</li><li>Services</li><li>Projects</li><li>Testimonials</li><li>Support</li><li>Careers</li><li>Contact Us</li>
  </ul>

  <h4 class="footer-head" style="left:533px">Contact Info</h4>
  <div class="contact-row" style="top:86px">
    <svg width="16" height="22" viewBox="0 0 16 22"><path d="M8 0a8 8 0 0 1 8 8c0 6-8 14-8 14S0 14 0 8a8 8 0 0 1 8-8z" fill="#f58a21"/><circle cx="8" cy="8" r="3" fill="#1f2329"/></svg>
    <div><strong style="color:#fff">Kelvan Development</strong><br>418 Marlow Ave.<br>Houston,<br>Texas 77031</div>
  </div>
  <div class="contact-row" style="top:212px">
    <svg width="18" height="18" viewBox="0 0 18 18"><path d="M3 1l4 0 1 4-2 2c1 2 3 4 5 5l2-2 4 1v4c-8 1-15-6-14-14z" fill="#f58a21"/></svg>
    <div>(713) 555-0148</div>
  </div>
  <div class="contact-row" style="top:246px">
    <svg width="18" height="14" viewBox="0 0 18 14"><rect width="18" height="14" fill="#f58a21"/><path d="M0 0l9 7 9-7" fill="none" stroke="#1f2329" stroke-width="1.5"/></svg>
    <div style="font-style:italic">info@kelvanbrook.com</div>
  </div>

  <h4 class="footer-head" style="left:737px">Contact Form</h4>
  <div class="field" style="left:737px;top:80px;width:188px;height:44px">Enter Name</div>
  <div class="field" style="left:933px;top:80px;width:189px;height:44px">Enter Email</div>
  <div class="field" style="left:737px;top:127px;width:385px;height:83px">Message</div>
  <span class="btn submit">Submit</span>
</footer>
<div class="bottom-bar">© Kelvan Development Group, Inc - 2017. All Rights Reserved.</div>

</body>
</html>
```